KAJU Freightways #ALLKAJU Business Cards & Letterhead

I am looking to business cards designed for our organization. We are currently undergoing a small re-branding that is taking place. Our organization is called KAJU Freightways and we are headquartered in Phoenix, AZ. We primarily provide transportation and logistics services to the Marlow Parcel Bureau who is our largest customer. I would like to see a design that incorporates name, title, contact info, website, and address (this will be different depending on the employee). I would also like to see some color on the business card using our logo colors or a variation. I would like our logo on the back of the business card with the website displayed. The final design should communicate that we are a next generation transportation operate that focuses on being driver-first, customer-centric, innovative, and sustainable.We would also like our #ALLKAJU catch phrase incorporated as well.

Target Market(s)

Transportation & Logistics

Industry/Entity Type

Trucking Company

Contact Information for Business Card

-First and Last Name
-Position Title
-Contact Phone
-Contact Email
-Physical Address

Font styles to use
Serif

Colors

Designer to choose colors to be used in the design.

Requirements
Must have
• -KAJU logo prominently displayed
• -#ALLKAJU catch phrase used
• -Some amount of color, design gradient, etc.
• -Logo on the back with website listed (https://www.kajufreightco.example)

```html
<!DOCTYPE html>
<html lang="en">
<head>
<meta charset="utf-8">
<title>KAJU Freightways Stationery</title>
<link rel="stylesheet" href="https://fonts.googleapis.com/css2?family=Lato:wght@400;700&family=Arimo:wght@400;700&display=swap">
<style>
  :root {
    --backdrop: #e4e4e4;
    --paper: #f5f5f5;
    --ink: #1b1b1b;
    --teal: #153a45;
    --green: #7bbd42;
    --white: #ffffff;
  }
  * { box-sizing: border-box; margin: 0; padding: 0; }
  html, body { width: 1200px; height: 1200px; overflow: hidden; }
  body {
    position: relative;
    background: var(--backdrop);
    font-family: "Lato", sans-serif;
    color: var(--teal);
  }

  /* ---------- Letterhead ---------- */
  .letterhead {
    position: absolute; left: 83px; top: 147px;
    width: 697px; height: 900px;
    background: var(--paper);
    box-shadow: 2px 3px 6px rgba(0,0,0,.35);
  }
  .side-band {
    position: absolute; top: 0; bottom: 0;
    background: var(--teal);
  }
  .side-band::before {
    content: ""; position: absolute; left: 0; right: 0; top: 0;
    height: var(--green-h); background: var(--green);
  }
  .letterhead .side-band { left: 36px; width: 50px; --green-h: 42px; }
  .brand-disc {
    position: absolute; border-radius: 50%;
    background: var(--white);
    display: flex; align-items: center; justify-content: center;
    font-family: "Lato", sans-serif; font-weight: 700;
    color: var(--teal); letter-spacing: .5px;
  }
  .letterhead .brand-disc { left: 20px; top: 36px; width: 84px; height: 84px; font-size: 22px; }
  .divider { position: absolute; width: 1.5px; background: var(--teal); }
  .letterhead .divider { left: 121px; top: 34px; height: 89px; }
  .tagline {
    position: absolute; color: var(--green); font-weight: 400; line-height: 1.15;
  }
  .letterhead .tagline { left: 136px; top: 60px; font-size: 16px; }
  .company-block {
    position: absolute; left: 323px; top: 59px;
    font-size: 10px; line-height: 12.5px; color: var(--teal);
  }
  .company-block strong { font-weight: 700; }
  .contact-list { position: absolute; list-style: none; color: var(--teal); }
  .letterhead .contact-list { left: 538px; top: 59px; font-size: 10px; line-height: 12.5px; }
  .contact-list li { display: flex; align-items: center; gap: 4px; white-space: nowrap; }
  .contact-list svg { width: 8px; height: 8px; flex: none; }
  .hashtag-vertical {
    position: absolute; left: 61px; top: 816px;
    transform: translate(-50%, 0) rotate(90deg); transform-origin: center;
    font-size: 10px; letter-spacing: .4px; color: var(--white); white-space: nowrap;
  }
  .hashtag-vertical .hash, .card-hashtag .hash { color: var(--green); }

  .letter-body {
    position: absolute; left: 132px; top: 204px; width: 507px;
    font-family: "Arimo", sans-serif; font-size: 9.9px; line-height: 13.7px; color: var(--ink);
  }
  .letter-date { margin-bottom: 14px; }
  .recipient { margin-bottom: 35px; }
  .salutation { font-weight: 700; margin-bottom: 27px; }
  .letter-body p.copy { text-align: justify; margin-bottom: 13.7px; }
  .closing { margin-top: 32px; }
  .signature-mark {
    width: 140px; height: 20px; margin: 14px 0 11px;
    background: linear-gradient(90deg, rgba(27,27,27,.18), rgba(27,27,27,.06));
    border-radius: 3px;
  }

  /* ---------- Business card: logo side ---------- */
  .card { position: absolute; left: 840px; width: 287px; height: 164px; box-shadow: 2px 3px 5px rgba(0,0,0,.35); overflow: hidden; }
  .card-logo-side { top: 273px; background: var(--teal); }
  .card-logo-side .brand-disc { left: 59px; top: 54px; width: 56px; height: 56px; font-size: 15px; }
  .card-logo-side .divider { left: 126px; top: 51px; height: 61px; background: var(--white); width: 1px; }
  .card-logo-side .tagline { left: 137px; top: 70px; font-size: 10.5px; }
  .card-web {
    position: absolute; left: 0; right: 0; top: 141px; text-align: center;
    font-size: 7.2px; letter-spacing: 1px; color: var(--white);
  }
  .card-web span { color: var(--green); }

  /* ---------- Business card: contact side ---------- */
  .card-contact-side { top: 461px; background: var(--paper); }
  .card-contact-side .side-band { left: 30px; width: 47px; --green-h: 22px; }
  .card-contact-side .brand-disc { left: 22px; top: 21px; width: 63px; height: 63px; font-size: 16px; }
  .card-hashtag { position: absolute; left: 34px; top: 138px; font-size: 7.5px; color: var(--white); letter-spacing: .2px; }
  .person-name { position: absolute; left: 113px; top: 40px; font-size: 10.2px; font-weight: 700; color: var(--green); letter-spacing: .2px; }
  .person-title { position: absolute; left: 113px; top: 52px; font-size: 7.5px; color: var(--teal); }
  .card-company { position: absolute; left: 113px; top: 85px; font-size: 7px; line-height: 9.5px; }
  .card-company strong { font-weight: 700; }
  .card-contact-side .contact-list { left: 113px; top: 122px; font-size: 7px; line-height: 9.5px; }
  .card-contact-side .contact-list svg { width: 6px; height: 6px; }
</style>
</head>
<body>

<svg width="0" height="0" style="position:absolute" aria-hidden="true">
  <defs>
    <symbol id="icon-phone" viewBox="0 0 10 10"><path fill="#7bbd42" d="M2 .5 3.6 2.7 2.7 3.8c.7 1.5 1.9 2.7 3.5 3.5l1.1-.9L9.5 8 8.3 9.5C4.3 9.3.7 5.7.5 1.7Z"/></symbol>
    <symbol id="icon-mail" viewBox="0 0 10 10"><rect x=".8" y="2" width="8.4" height="6" fill="none" stroke="#7bbd42" stroke-width="1"/><path d="M.8 2 5 5.6 9.2 2" fill="none" stroke="#7bbd42" stroke-width="1"/></symbol>
    <symbol id="icon-web" viewBox="0 0 10 10"><circle cx="5" cy="5" r="4.2" fill="none" stroke="#7bbd42" stroke-width=".9"/><ellipse cx="5" cy="5" rx="1.8" ry="4.2" fill="none" stroke="#7bbd42" stroke-width=".8"/><path d="M.8 5h8.4M1.6 3h6.8M1.6 7h6.8" stroke="#7bbd42" stroke-width=".7"/></symbol>
  </defs>
</svg>

<section class="letterhead">
  <div class="side-band"></div>
  <div class="brand-disc">KAJU</div>
  <div class="divider"></div>
  <div class="tagline">Transportation<br>and Energy Services</div>
  <div class="company-block">
    <strong>KAJU Freightways &amp; Energy Services, Inc.</strong><br>
    4410 North Saguaro Ridge Road<br>
    Mesa, AZ 85201
  </div>
  <ul class="contact-list">
    <li><svg><use href="#icon-phone"/></svg>555-014-2297</li>
    <li><svg><use href="#icon-mail"/></svg>info@kajufreightco.example</li>
    <li><svg><use href="#icon-web"/></svg>www.kajufreightco.example</li>
  </ul>
  <div class="hashtag-vertical"><span class="hash">#</span>ALLKAJU</div>

  <div class="letter-body">
    <div class="letter-date">November 15, 2019</div>
    <div class="recipient">Mr. John Doe<br>President<br>AA Corporation<br>111 Street Name, Suite#<br>City, State, 12345</div>
    <div class="salutation">Dear Mr. John,</div>
    <p class="copy">Lorem ipsum dolor sit amet, consectetur adipiscing elit. Integer diam quam, egestas eu ultrices eu, suscipit ac sapien. Phasellus eu dui nisi. Nam et euismod diam, nec lobortis tortor. Donec et diam nulla. Aenean varius tincidunt convallis. Aliquam a tortor at lacus dictum aliquet. Nunc laoreet metus sapien, in scelerisque augue consectetur in.</p>
    <p class="copy">Fusce nec justo laoreet, egestas justo sed, aliquet sem. Pellentesque pharetra massa non orci bibendum semper. Pellentesque cursus eu lectus a consectetur. Nunc volutpat suscipit posuere. Vestibulum facilisis vel quam male-suada mattis. Nulla in mattis tellus. Maecenas tristique mauris vitae pharetra tincidunt. In ut ornare risus. Integer molestie vestibulum nisi, semper dapibus mi condimentum eu.</p>
    <p class="copy">Nullam sagittis elit libero, id fringilla est tincidunt eget. Donec in ipsum ultricies, consectetur quam vel, facilisis elit. Phasellus tincidunt congue risus vel luctus. Suspendisse ut mollis neque. Donec ornare orci in turpis vestibulum, in ultrices metus scelerisque. Pellentesque mattis mattis nunc, nec tincidunt lacus egestas id. Fusce facilisis sagittis neque sit amet vulputate. Aliquam ut eros lobortis tortor facilisis vehicula. Sed sed luctus leo, at laoreet sapien. Donec placerat adipiscing ligula non euismod. In lobortis pretium nisl id luctus.</p>
    <p class="copy">Integer gravida tincidunt nibh, scelerisque tincidunt turpis. Suspendisse potenti. Nunc hendrerit euismod lectus id elementum. Fusce vitae gravida velit, quis eleifend lectus. In imperdiet mauris eu dui viverra sagittis. Donec tempor dui diam, condimentum gravida lacus pretium a. Nullam fringilla augue quis arcu placerat scelerisque. Aliquam nec tincidunt augue, sit amet posuere ipsum.</p>
    <div class="closing">Sincerely Yours,</div>
    <div class="signature-mark" role="img" aria-label="Handwritten signature of Rowan Delacroix"></div>
    <div class="signer">Rowan Delacroix<br>President</div>
  </div>
</section>

<section class="card card-logo-side">
  <div class="brand-disc">KAJU</div>
  <div class="divider"></div>
  <div class="tagline">Transportation<br>and Energy Services</div>
  <div class="card-web">www.<span>kajufreightco</span>.example</div>
</section>

<section class="card card-contact-side">
  <div class="side-band"></div>
  <div class="brand-disc">KAJU</div>
  <div class="card-hashtag"><span class="hash">#</span>ALLKAJU</div>
  <div class="person-name">ROWAN DELACROIX</div>
  <div class="person-title">President</div>
  <div class="card-company">
    <strong>KAJU Freightways &amp; Energy Services, Inc.</strong><br>
    4410 North Saguaro Ridge Road<br>
    Mesa, AZ 85201
  </div>
  <ul class="contact-list">
    <li><svg><use href="#icon-phone"/></svg>555-014-2297</li>
    <li><svg><use href="#icon-mail"/></svg>rowan@kajufreightco.example</li>
    <li><svg><use href="#icon-web"/></svg>www.kajufreightco.example</li>
  </ul>
</section>

</body>
</html>
```